San Francisco Leading Consulting firm - 47Vora Web Design Project

•Create a Web Design
•Uncoded webpage layout design
•2 Pages Design - Homepage + Interior Page

Task Description
Hello, we're looking for a re-design our current website www.47vora-example.com

we have a sample mockup design @

http://47vora.pubtrellis-example.org/

This shows the layout that we like and also a sample of 6 pictures that would change based on where you mouse over..

6 pictures HOME design needs to be included.

SMART
THOUGHTFUL
FLEXIBLE
CREATIVE SERVICES
TECHNICAL SERVICES
PARTNERS

sites we like:

http://www.melvanadvisory-example.com/Home.cfm?id=Home
http://www.plinthworks-example.com/index.html

Our company can be best described as: 100+ employees, cutting-edge, depandable, innovative, strong, smart.

Our Primary focus is: IT Consulting Services and Creative Design services

47Vora LLC is a consulting firm providing creative design, business and technology solutions to both private and public interests.

Established in 1996, 47Vora is a San Francisco based company providing specialists for a range of business needs including:

Creative Design Services
•Print
•Logo Design
•Website Design
•Illustration

and

Business and Technology solutions

•Application Software and Web Development
•Business Process Re-Design (BPR)
•Business/Systems Analysis and Requirement Documentation
•Mentoring and Training
•Network/Hardware Installation Services
•System Design and Architecture
•Vendor Management
•Docuvault Architecture and Implementation

our sample mockup site:

Reason: Due to holiday season, we're not available to work with designers and finilize our design.  

Thank you very much for submitting your design.

We appreciate your time and creativity.   Since, our office is currently closed for holidays, we will be reviewing it in details next week and will make our decision as soon as possible.

It would be great if you could submit any of your changes by Wed next week, so it would be part of our reviews. 

Please see updated wireframe under attachments:  we have some minor updates to our wireframe that we would like you to update your designs, if possible.  

We also encorouge you not to use our standard wireframe and come up with more unique designs.   Everything would be considered when we review your design.

 

Ringpost Market(s)

Creative services and professional services clients, including government agencies

Industry/Entity Type

Business

Requirements
Must have
• Clean, professional look, easy navigation

```html
<!DOCTYPE html>
<html lang="en">
<head>
<meta charset="utf-8">
<title>47Vora — Technical Services</title>
<link href="https://fonts.googleapis.com/css2?family=Arimo:wght@400;700&family=Roboto+Condensed:wght@400&display=swap" rel="stylesheet">
<style>
:root{
  --blue:#0e8fc6;
  --blue-dark:#0a78aa;
  --blue-light:#5cc3ea;
  --text:#333;
  --muted:#6b6b6b;
  --rule:#c9c9c9;
  --white:#fff;
}
*{margin:0;padding:0;box-sizing:border-box}
html,body{width:1200px;height:1100px;overflow:hidden;background:var(--white)}
body{position:relative;font-family:"Arimo",Arial,sans-serif;color:var(--text)}
.abs{position:absolute}

.brand{left:136px;top:26px;display:flex;align-items:center;gap:10px}
.brand-dot{width:26px;height:26px;border-radius:50%;background:var(--blue)}
.brand-name{font-size:30px;color:#555;font-weight:400;letter-spacing:1px}

.main-nav{left:346px;top:40px;display:flex;font-size:14.5px;color:#555}
.main-nav a{color:inherit;text-decoration:none;padding:0 12px;border-left:1px solid var(--blue);line-height:18px}
.main-nav a:first-child{border-left:0;padding-left:8px}

.contact{left:929px;top:13px;font-size:12px;line-height:18px;color:#222}
.contact .hl{color:var(--blue);font-weight:700}

.hero{left:0;top:93px;width:1200px;height:487px;background:linear-gradient(180deg,#f2f2f2 0%,#d8d8d8 45%,#9c9c9c 80%,#7a7a7a 100%)}
.slide{left:139px;top:131px;width:920px;height:399px;border-radius:10px;background:var(--white);overflow:hidden}
.slide-photo{left:0;top:0;width:920px;height:352px;background:linear-gradient(90deg,#f4f4f4 0%,#eef0f1 45%,#d9dcde 70%,#c5b6a8 85%,#d8d8d8 100%)}
.slide-strip{left:0;top:352px;width:920px;height:47px;background:linear-gradient(180deg,#c8c8c8,#e6e6e6)}
.ribbon{left:118px;top:160px}
.slide-title{left:219px;top:254px;font-size:50px;font-weight:700;color:#111;letter-spacing:-0.5px}
.slide-sub{left:223px;top:304px;font-family:"Roboto Condensed",sans-serif;font-size:23px;line-height:25px;color:var(--white)}
.dots{left:521px;top:501px;display:flex;gap:14px}
.dots span{width:14px;height:14px;border-radius:50%;background:#111}
.dots span.on{background:var(--blue)}
.arrow{top:280px}

.card{top:602px;width:300px;height:130px;border:1px solid var(--blue);border-radius:4px;overflow:hidden;background:var(--white)}
.card-head{height:27px;background:linear-gradient(180deg,#1ea3d8,var(--blue-dark));color:var(--white);font-size:15px;font-weight:700;padding:4px 16px}
.card-art{position:absolute;top:34px;height:96px}
.card-plus{position:absolute;right:0;bottom:0}

.rule{left:122px;width:960px;height:1px;background:var(--rule)}
.featured{left:124px;top:770px;font-size:18px;font-weight:700;line-height:20px;color:#222}
.featured-arrow{left:222px;top:772px}
.clients{left:290px;top:776px;width:790px;display:flex;justify-content:space-between;align-items:center;font-size:14px;font-weight:700;color:#666}
.client{display:flex;align-items:center;gap:5px}
.client i{width:10px;height:10px;border-radius:50%;background:#888;display:block}

.svc-list{font-size:14.5px;line-height:24px;color:var(--muted);list-style:none}

.news{left:123px;top:975px;width:960px;height:40px;border:1px solid var(--blue);border-radius:7px;overflow:hidden}
.news-tag{position:absolute;left:0;top:0}
.news-label{position:absolute;left:17px;top:11px;color:var(--white);font-size:14.5px;font-weight:700}
.news-text{position:absolute;left:164px;top:9px;font-size:13px;color:#222}

.copyright{left:119px;top:1058px;font-size:12.5px;color:#222}
.foot-nav{left:530px;top:1058px;display:flex;gap:30px;font-size:12.5px}
.foot-nav a{color:var(--blue);text-decoration:none}
</style>
</head>
<body>

<header>
  <div class="abs brand"><span class="brand-dot"></span><span class="brand-name">47Vora</span></div>
  <nav class="abs main-nav">
    <a href="#">Company</a><a href="#">Creative Services</a><a href="#">Technical Services</a><a href="#">Partners</a><a href="#">Contact Us</a>
  </nav>
  <address class="abs contact" style="font-style:normal">
    2270 Harlow St, Ste 810<br>San Francisco, CA 94199<br>
    <span class="hl">415-555-0147</span><br><span class="hl">info@47vora-example.com</span>
  </address>
</header>

<section>
  <div class="abs hero" role="img" aria-label="Black and white city skyline photograph"></div>
  <div class="abs slide">
    <div class="abs slide-photo" role="img" aria-label="Consultant sketching a database diagram on a glass board"></div>
    <div class="abs slide-strip"></div>
  </div>
  <svg class="abs ribbon" width="962" height="310" viewBox="0 0 962 310">
    <path d="M0 0 C200 60 300 140 420 155 C540 140 740 60 962 0 L962 310 C740 250 540 175 420 168 C300 175 200 250 0 310 Z" fill="#0d96cf" opacity="0.85"/>
    <path d="M0 30 C220 90 330 150 430 158 C540 150 720 90 962 30 L962 60 C720 110 540 156 430 162 C330 156 220 110 0 60 Z" fill="#8fd8f2" opacity="0.8"/>
  </svg>
  <h1 class="abs slide-title">Technical Services</h1>
  <p class="abs slide-sub">Our experience will keep<br>your projects on track.</p>
  <div class="abs dots"><span class="on"></span><span></span><span></span><span></span><span></span><span></span></div>
  <svg class="abs arrow" style="left:124px" width="30" height="52" viewBox="0 0 30 52"><path d="M26 2 L6 26 L26 50" fill="none" stroke="#fff" stroke-width="6"/></svg>
  <svg class="abs arrow" style="left:1046px" width="30" height="52" viewBox="0 0 30 52"><path d="M4 2 L24 26 L4 50" fill="none" stroke="#fff" stroke-width="6"/></svg>
</section>

<section>
  <div class="abs card" style="left:126px">
    <div class="card-head">Creative Services</div>
    <div class="card-art" role="img" aria-label="Colourful abstract swirl illustration" style="left:40px;width:210px;background:radial-gradient(ellipse at 50% 90%,#f27ad6 0%,#ffd25a 30%,#7dd3f0 55%,rgba(255,255,255,0) 75%)"></div>
    <svg class="card-plus" width="42" height="42" viewBox="0 0 42 42"><path d="M42 0 L42 42 L0 42 Z" fill="var(--blue)"/><path d="M30 22 V36 M23 29 H37" stroke="#fff" stroke-width="3"/></svg>
  </div>
  <div class="abs card" style="left:452px">
    <div class="card-head">Business &amp; Technical Services</div>
    <div class="card-art" role="img" aria-label="Metal gears illustration" style="left:35px;width:210px;background:radial-gradient(ellipse at 50% 60%,#8a8a8a 0%,#b8b8b8 40%,rgba(255,255,255,0) 72%)"></div>
    <svg class="card-plus" width="42" height="42" viewBox="0 0 42 42"><path d="M42 0 L42 42 L0 42 Z" fill="var(--blue)"/><path d="M30 22 V36 M23 29 H37" stroke="#fff" stroke-width="3"/></svg>
  </div>
  <div class="abs card" style="left:776px">
    <div class="card-head">Partners</div>
    <div class="card-art" role="img" aria-label="Blue globe illustration" style="left:100px;top:30px;width:102px;height:100px;border-radius:50%;background:radial-gradient(circle at 40% 35%,#bfe9f8 0%,#3aa9d8 55%,#156d9c 100%)"></div>
    <svg class="card-plus" width="42" height="42" viewBox="0 0 42 42"><path d="M42 0 L42 42 L0 42 Z" fill="var(--blue)"/><path d="M30 22 V36 M23 29 H37" stroke="#fff" stroke-width="3"/></svg>
  </div>
</section>

<section>
  <div class="abs rule" style="top:753px"></div>
  <h2 class="abs featured">Featured<br>Clients</h2>
  <svg class="abs featured-arrow" width="22" height="38" viewBox="0 0 22 38"><path d="M4 2 L17 19 L4 36" fill="none" stroke="var(--blue)" stroke-width="5"/></svg>
  <div class="abs clients">
    <span class="client"><i></i>Ringpost</span>
    <span class="client">Larkfield</span>
    <span class="client">Norvex</span>
    <span class="client">Calder</span>
    <span class="client">Vantor</span>
    <span class="client">Telwave</span>
    <span class="client">Brevity</span>
    <span class="client">Holloway</span>
    <span class="client">Fizzwell</span>
  </div>
  <div class="abs rule" style="top:824px"></div>
</section>

<section>
  <ul class="abs svc-list" style="left:128px;top:850px">
    <li>Application Software and Web Development</li><li>Business Process Re-Design (BPR)</li><li>Systems Analysis and Requirement Docs</li><li>Mentoring and Training</li>
  </ul>
  <ul class="abs svc-list" style="left:452px;top:848px">
    <li>Network/Hardware Installation Services</li><li>System Design and Architecture</li><li>Vendor Management</li><li>Docuvault Architecture and Implementation</li>
  </ul>
  <ul class="abs svc-list" style="left:776px;top:843px">
    <li>Print &amp; Package Design</li><li>Brand and Identity Creation</li><li>Website and User Experience Design</li><li>Illustration Design</li>
  </ul>
</section>

<section class="abs news">
  <svg class="news-tag" width="140" height="40" viewBox="0 0 140 40"><path d="M0 0 H125 L137 19 L125 40 H0 Z" fill="var(--blue)"/></svg>
  <span class="news-label">Latest News</span>
  <span class="news-text">Updated news item for the day goes here</span>
</section>

<footer>
  <div class="abs rule" style="top:1039px"></div>
  <p class="abs copyright">Copyright 2011, 47Vora, LLC All rights reserved.</p>
  <nav class="abs foot-nav">
    <a href="#">Home</a><a href="#">Company</a><a href="#">Technical Services</a><a href="#">Creative Services</a><a href="#">Partners</a><a href="#">Contact Us</a>
  </nav>
</footer>

</body>
</html>
```